Business Card for Field Lotus-Eco Friendly Organic Clothing Brand

We are looking for an amazing business card for our eco friendly, organic clothing brand. We are thinking maybe a business card with a peel off sticker on the back, since our hanging clothing tag is a peel off sticker on the back. I will attach our hang tag so we can make sure we stay in line with our design. I've also attached a bag we are doing because I do like the scattered emblem look as well.

```html
<!DOCTYPE html>
<html lang="en">
<head>
<meta charset="utf-8">
<title>Field Lotus — Business Card</title>
<link href="https://fonts.googleapis.com/css2?family=Open+Sans:wght@400;600;700&display=swap" rel="stylesheet">
<style>
  :root {
    --backdrop: #8c8c8c;
    --paper: #f1f1f2;
    --ink: #1e1e1e;
    --ink-soft: #4a4a4a;
    --gold: #c49a2c;
    --gold-light: #e3c064;
    --night: #151515;
    --camo-dark: #1c1f14;
    --camo-mid: #2b3020;
    --rule: #9a9a9a;
  }
  * { box-sizing: border-box; margin: 0; padding: 0; }
  html, body {
    width: 1105px; height: 1200px; overflow: hidden;
    background: var(--backdrop);
    font-family: "Open Sans", Arial, sans-serif;
  }
  .card {
    position: absolute; left: 182px; width: 746px; height: 424px;
    overflow: hidden;
  }
  .card--front { top: 120px; background: var(--paper); }
  .card--back { top: 637px; background: var(--night); }

  .brand {
    position: absolute; display: flex; align-items: center; gap: 14px;
  }
  .brand__mark {
    width: 26px; height: 26px; background: var(--gold);
  }
  .brand__name {
    font-weight: 700; font-size: 34px; color: var(--gold); letter-spacing: .5px;
    white-space: nowrap;
  }
  .card--front .brand { left: 40px; top: 186px; }
  .card--back .brand { left: 50%; top: 50%; transform: translate(-50%, -50%); }
  .card--back .brand__name { font-size: 44px; color: var(--gold-light); }
  .card--back .brand__mark { width: 32px; height: 32px; background: var(--gold-light); }

  .divider {
    position: absolute; left: 343px; top: 102px; width: 1px; height: 192px;
    background: var(--rule);
  }
  .contact { position: absolute; left: 367px; top: 92px; color: var(--ink-soft); }
  .contact__name { font-size: 28px; font-weight: 600; color: var(--ink); line-height: 1.15; }
  .contact__role { font-size: 19px; color: var(--ink); margin-bottom: 14px; }
  .contact__address { font-size: 19px; margin-bottom: 12px; }
  .contact__list { list-style: none; }
  .contact__item {
    display: flex; align-items: center; gap: 10px; font-size: 19px; line-height: 29px;
  }
  .contact__icon { width: 17px; height: 17px; flex: none; fill: var(--gold); }

  .camo-band {
    position: absolute; left: 0; bottom: 0; width: 100%; height: 35px;
    background: linear-gradient(90deg, var(--camo-dark), var(--camo-mid) 40%, var(--camo-dark) 70%, var(--camo-mid));
  }
  .word-pattern {
    position: absolute; inset: 0;
    background: radial-gradient(ellipse at center, #1e1e1e 0%, var(--night) 75%);
  }
</style>
</head>
<body>
  <section class="card card--front">
    <div class="brand">
      <span class="brand__mark"></span>
      <span class="brand__name">Field Lotus</span>
    </div>
    <div class="divider"></div>
    <div class="contact">
      <p class="contact__name">Daniel Reyes</p>
      <p class="contact__role">CEO/Founder</p>
      <p class="contact__address">Coral Bend, FL&nbsp;&nbsp;33000</p>
      <ul class="contact__list">
        <li class="contact__item">
          <svg class="contact__icon" viewBox="0 0 24 24"><path d="M6.6 10.8a15.1 15.1 0 0 0 6.6 6.6l2.2-2.2a1 1 0 0 1 1-.25 11.4 11.4 0 0 0 3.6.57 1 1 0 0 1 1 1V20a1 1 0 0 1-1 1A17 17 0 0 1 3 4a1 1 0 0 1 1-1h3.5a1 1 0 0 1 1 1c0 1.25.2 2.45.57 3.57a1 1 0 0 1-.25 1z"/></svg>
          (800) 555-0142
        </li>
        <li class="contact__item">
          <svg class="contact__icon" viewBox="0 0 24 24"><path d="M6.6 10.8a15.1 15.1 0 0 0 6.6 6.6l2.2-2.2a1 1 0 0 1 1-.25 11.4 11.4 0 0 0 3.6.57 1 1 0 0 1 1 1V20a1 1 0 0 1-1 1A17 17 0 0 1 3 4a1 1 0 0 1 1-1h3.5a1 1 0 0 1 1 1c0 1.25.2 2.45.57 3.57a1 1 0 0 1-.25 1z"/></svg>
          (800) 555-0199
        </li>
        <li class="contact__item">
          <svg class="contact__icon" viewBox="0 0 24 24"><path d="M2 5h20v14H2z M2 5l10 8 10-8" fill="var(--gold)"/><path d="M3 6l9 7 9-7" fill="none" stroke="var(--paper)" stroke-width="1.6"/></svg>
          hello@fieldlotus.com
        </li>
        <li class="contact__item">
          <svg class="contact__icon" viewBox="0 0 24 24"><circle cx="12" cy="12" r="10"/><path d="M2 12h20M12 2c3 3 3 17 0 20M12 2c-3 3-3 17 0 20" fill="none" stroke="var(--paper)" stroke-width="1.4"/></svg>
          www.fieldlotus.com
        </li>
      </ul>
    </div>
    <div class="camo-band" role="img" aria-label="Dark olive camouflage pattern band"></div>
  </section>

  <section class="card card--back">
    <div class="word-pattern" role="img" aria-label="Faint scattered pattern of peace words, hearts and peace signs on black"></div>
    <div class="brand">
      <span class="brand__mark"></span>
      <span class="brand__name">Field Lotus</span>
    </div>
  </section>
</body>
</html>
```